KR Appraisals website redesign

I would like to refresh my existing website of www.krappraisals-example.com with new graphics, look and feel, as well as updated structure and wording. Content and layout changes have been uploaded to this project Brief.

My existing website has a dark feel. I am now looking for a light and energetic feel. Financial Services is my industry, so the website should be reflect that. I would also like to reflect the concepts of Trust, Service and Expertise.

The website must be serious and upmarket.

Target Market(s)

Corporate board members, CFO's, treasurers and controllers
Auditors, tax advisors, private equity and venture capital asset managers, investors, tax authorities

Industry/Entity Type

Financial Service

Coding

Coded - Design and coding required

Number of Pages Required

5+ page

Font styles to use
Sans Serif
Other font styles liked:
• Designer can choose another modern font

Colors
0355a3
3277b5
85acd3
eaf1f7
f37122
f68d4d
9bcb3c
acd037
cadf82

Requirements
Must have
• Good hi resolution pictures that convey "Finance", "Trust", "Service" or "Expertise".
• An anti-bot (such as Captcha) mechanism in the contact form.
Should not have
• Must not have all content on one rolling screen.

```html
<!DOCTYPE html>
<html lang="en">
<head>
<meta charset="utf-8">
<title>KR Appraisals – Our Services</title>
<link rel="stylesheet" href="https://fonts.googleapis.com/css2?family=Nunito:wght@400;600;700&family=Montserrat:wght@500;600&display=swap">
<style>
:root{
  --orange:#f37122;
  --green:#9bcb3c;
  --blue:#0355a3;
  --nav-grey:#6f6f6f;
  --text-grey:#666;
  --panel:#f2f2f2;
  --footer:#333333;
  --footer-text:#9a9a9a;
  --footer-line:#666;
  --white:#ffffff;
}
*{margin:0;padding:0;box-sizing:border-box}
html,body{width:1200px;height:1144px;overflow:hidden;background:var(--white)}
body{position:relative;font-family:"Nunito",sans-serif;color:var(--text-grey)}
.site-header{position:absolute;left:0;top:0;width:1200px;height:100px;
  background:linear-gradient(90deg,#e6e6dc 0%,#eeeee2 45%,#f6f6e6 100%)}
.brand{position:absolute;display:flex;align-items:center;gap:8px;
  font-family:"Montserrat",sans-serif;font-weight:500;color:#7a7a7a;letter-spacing:1px}
.brand .mark{width:12px;height:12px;background:#7a7a7a}
.header-brand{left:161px;top:38px;font-size:20px}
.main-nav{position:absolute;top:45px;left:611px;display:flex;gap:0;
  font-family:"Montserrat",sans-serif;font-size:11px;font-weight:600}
.main-nav a{position:absolute;white-space:nowrap;color:var(--nav-grey);text-decoration:none}
.main-nav .active{color:var(--blue)}
.page-title{position:absolute;top:186px;left:0;width:1200px;text-align:center;
  font-family:"Montserrat",sans-serif;font-weight:600;font-size:38px;color:var(--orange);letter-spacing:-0.5px}
.service-panel{position:absolute;left:562px;top:281px;width:477px;height:420px;background:var(--panel)}
.service-photo{position:absolute;left:161px;top:341px;width:439px;height:292px;
  background:linear-gradient(135deg,#e9eef3 0%,#cfdbe6 45%,#f1efe9 100%)}
.service-title{position:absolute;left:639px;top:355px;width:360px;
  font-family:"Montserrat",sans-serif;font-weight:600;font-size:30px;line-height:38px;color:var(--green)}
.service-text{position:absolute;left:639px;top:453px;width:362px;font-size:10.5px;line-height:18.75px;color:var(--text-grey)}
.site-footer{position:absolute;left:0;top:0;width:1200px;height:1144px;pointer-events:none}
.footer-brand{left:508px;top:858px;font-size:20px;color:#8a8a8a}
.footer-brand .mark{background:#8a8a8a}
.footer-rule{position:absolute;left:161px;width:879px;height:1px;background:var(--footer-line)}
.footer-nav a{position:absolute;top:951px;font-family:"Montserrat",sans-serif;font-size:11px;font-weight:600;color:#8e8e8e;text-decoration:none;white-space:nowrap}
.footer-nav .active{color:var(--green)}
.footer-col{position:absolute;top:1007px;font-size:10.5px;color:var(--footer-text)}
.footer-col h3{font-family:"Montserrat",sans-serif;font-weight:600;font-size:13px;color:var(--orange);margin-bottom:11px}
.footer-col p{line-height:22.5px}
.footer-col .hl{color:var(--green)}
.footer-col .wh{color:#e6e6e6}
.contact-line{position:relative;padding-left:20px;line-height:16.5px}
.contact-line svg{position:absolute;left:0;top:1px}
.address{margin-bottom:9px}
.phone{color:#f0f0f0;font-size:11.5px;font-weight:600}
.badge{position:absolute;background:#5a5a5a}
</style>
</head>
<body>
<header class="site-header">
  <div class="brand header-brand"><span class="mark"></span>KR APPRAISALS</div>
  <nav class="main-nav">
    <a style="left:0">HOME</a>
    <a style="left:75px">ABOUT</a>
    <a class="active" style="left:155px">SERVICES</a>
    <a style="left:250px">NEWS &amp; VIEWS</a>
    <a style="left:374px">CONTACT</a>
  </nav>
</header>

<h1 class="page-title">OUR SERVICES</h1>

<section>
  <div class="service-panel"></div>
  <div class="service-photo" role="img" aria-label="Photo of colleagues reviewing financial charts on a tablet and printed reports beside a cup of coffee"></div>
  <h2 class="service-title">PURCHASE PRICE<br>ALLOCATION</h2>
  <p class="service-text">Accounting procedures require an acquiror to allocate purchase consideration to the fair value of all acquired assets and liabilities when obtaining control of a company. This process, called a purchase price allocation (PPA), involves assets and liabilities that did not exist on the target’s balance sheet prior to the transaction. Certain pre-existing assets must be restated to fair value. This process can be time consuming and complex. KR Appraisals has a wealth of experience in this area and can work with you and your independent auditor to achieve a smooth process.</p>
</section>

<footer>
  <svg class="site-footer" width="1200" height="1144" viewBox="0 0 1200 1144">
    <polygon points="0,859 600,791 1200,859 1200,1144 0,1144" fill="#333333"/>
  </svg>
  <div class="brand footer-brand"><span class="mark"></span>KR APPRAISALS</div>
  <div class="footer-rule" style="top:936px"></div>
  <nav class="footer-nav">
    <a class="active" style="left:386px">HOME</a>
    <a style="left:461px">ABOUT</a>
    <a style="left:541px">SERVICES</a>
    <a style="left:636px">NEWS &amp; VIEWS</a>
    <a style="left:760px">CONTACT</a>
  </nav>
  <div class="footer-rule" style="top:981px"></div>

  <div class="footer-col" style="left:163px">
    <h3>CREDITS</h3>
    <p>© 2019 <span class="hl">KR Appraisals</span></p>
    <p>Logo by <span class="wh">Mara Lindqvist</span></p>
    <p>Website by <span class="hl">Brightline Webworks</span></p>
  </div>

  <div class="footer-col" style="left:389px">
    <h3>LEIDEN</h3>
    <div class="contact-line address">
      <svg width="9" height="12" viewBox="0 0 9 12"><path d="M4.5 0A4.5 4.5 0 0 0 0 4.5C0 8 4.5 12 4.5 12S9 8 9 4.5A4.5 4.5 0 0 0 4.5 0z" fill="#9bcb3c"/><circle cx="4.5" cy="4.5" r="1.7" fill="#333"/></svg>
      Kanaalweg 48<br>2321 AB Leiden
    </div>
    <div class="contact-line phone">
      <svg width="12" height="12" viewBox="0 0 12 12"><path d="M2.5 0.5l2 2.5-1.2 1.5c.8 1.7 2.3 3.2 4 4l1.5-1.2 2.5 2-1.3 2C5.5 11 1 6.5.5 1.8z" fill="#9bcb3c"/></svg>
      070 555 0142
    </div>
  </div>

  <div class="footer-col" style="left:616px">
    <h3>AMSTERDAM</h3>
    <div class="contact-line address">
      <svg width="9" height="12" viewBox="0 0 9 12"><path d="M4.5 0A4.5 4.5 0 0 0 0 4.5C0 8 4.5 12 4.5 12S9 8 9 4.5A4.5 4.5 0 0 0 4.5 0z" fill="#9bcb3c"/><circle cx="4.5" cy="4.5" r="1.7" fill="#333"/></svg>
      Zuidplein 14<br>1077 XV Amsterdam
    </div>
    <div class="contact-line phone">
      <svg width="12" height="12" viewBox="0 0 12 12"><path d="M2.5 0.5l2 2.5-1.2 1.5c.8 1.7 2.3 3.2 4 4l1.5-1.2 2.5 2-1.3 2C5.5 11 1 6.5.5 1.8z" fill="#9bcb3c"/></svg>
      020 555 0187
    </div>
  </div>

  <div class="badge" role="img" aria-label="Professional institute membership badge" style="left:856px;top:1001px;width:170px;height:36px;border-radius:4px"></div>
  <div class="badge" role="img" aria-label="Appraisers society membership badge" style="left:854px;top:1048px;width:170px;height:70px;border-radius:4px"></div>
</footer>
</body>
</html>
```